Talvoro bonds (Surety bond broker)

We are a broker of surety bonds, we need a presentation and a flyer with fresh design. Our core values are reliable, on time and customized service. We want to transmit to our clients, they can leave on us the process of underwriting and issuing a surety bond, so they can focus on their business with no distractions.

Font styles to use
Sans Serif
Other font styles liked:

Requirements
Must have
• Visually attractive.
Main Message: Fast service issuing and underwriting surety bonds, reliable, nos surprises, we are always one step ahead, customized and personalized bonding solutions.
Nice to have
• Have short version for the flyer, and extended version for the presentation.
Should not have
• We already have a logo (attached), maintain colors

```html
<!DOCTYPE html>
<html lang="es">
<head>
<meta charset="utf-8">
<title>Talvoro bonds — Folleto</title>
<link href="https://fonts.googleapis.com/css2?family=Zilla+Slab:wght@400;500;600&display=swap" rel="stylesheet">
<style>
  :root{
    --paper:#f6f4ef;
    --green:#4f9a3e;
    --green-light:#8cc063;
    --green-wash:#cfe6b4;
    --charcoal:#3a3a3a;
    --ink:#3c3c3c;
    --sand:#c9a774;
    --sky:#b9b16a;
    --steel:#5d6b70;
  }
  *{margin:0;padding:0;box-sizing:border-box}
  html,body{width:1200px;height:900px;overflow:hidden;background:var(--paper)}
  body{font-family:"Zilla Slab",Georgia,serif;color:var(--ink)}
  .spread{position:absolute;left:30px;top:190px;width:1140px;height:520px;background:#fff;box-shadow:0 6px 24px rgba(0,0,0,.12);overflow:hidden}
  .spread-art{position:absolute;inset:0}
  .index-panel{position:absolute;left:210px;top:52px;width:260px}
  .panel-title{font-weight:500;color:var(--green);font-size:42px;line-height:.95}
  .index-list{list-style:none;margin-top:26px}
  .index-list li{font-size:15.5px;line-height:1;margin-bottom:20px;color:var(--ink)}
  .index-list .num{color:#777;margin-right:6px}
  .index-list .sep{color:var(--green-light);margin-right:6px}
  .about-panel{position:absolute;left:490px;top:40px;width:270px}
  .about-panel .panel-title{font-size:40px}
  .about-text{margin-top:18px;font-size:10.6px;line-height:1.28;color:var(--ink)}
  .about-text p{margin-bottom:11px}
  .brand{position:absolute;display:flex;align-items:center;gap:6px;font-weight:600;font-size:19px;letter-spacing:.5px;color:var(--green)}
  .brand .mark{width:9px;height:9px;background:var(--green)}
  .brand-index{left:350px;top:460px}
  .brand-about{left:490px;top:460px}
</style>
</head>
<body>
<section class="spread">
  <svg class="spread-art" width="1140" height="520" viewBox="0 0 1140 520">
    <defs>
      <linearGradient id="wash" x1="0" y1="0" x2="0.2" y2="1">
        <stop offset="0" stop-color="#bfe09e"/>
        <stop offset=".55" stop-color="#e4f1d6"/>
        <stop offset="1" stop-color="#ffffff"/>
      </linearGradient>
      <linearGradient id="pier" x1="0" y1="0" x2="0" y2="1">
        <stop offset="0" stop-color="#a9783c"/>
        <stop offset=".45" stop-color="#d8b57a"/>
        <stop offset="1" stop-color="#b89466"/>
      </linearGradient>
      <linearGradient id="port" x1="0" y1="0" x2="0" y2="1">
        <stop offset="0" stop-color="#5e6d6e"/>
        <stop offset=".35" stop-color="#c2b772"/>
        <stop offset=".7" stop-color="#7a7d6e"/>
        <stop offset="1" stop-color="#3f4a50"/>
      </linearGradient>
    </defs>
    <rect width="1140" height="520" fill="url(#wash)"/>
    <path role="img" aria-label="Fotografía: playa bajo un muelle de madera al atardecer" d="M0 0 H165 C150 180 135 350 95 520 H0 Z" fill="url(#pier)"/>
    <path d="M165 0 H200 C186 190 168 360 128 520 H95 C135 350 150 180 165 0 Z" fill="var(--charcoal)"/>
    <path d="M205 0 H214 C200 200 182 370 140 520 H128 C170 360 190 190 205 0 Z" fill="var(--green)"/>
    <path role="img" aria-label="Fotografía: grúas portuarias en un muelle de carga al atardecer" d="M800 0 H1140 V420 C1000 380 880 260 800 0 Z" fill="url(#port)"/>
    <path d="M755 0 H800 C880 260 1000 380 1140 420 V440 C990 410 850 290 755 0 Z" fill="var(--charcoal)"/>
    <path d="M735 0 H748 C840 300 990 430 1140 452 V470 C980 450 820 320 735 0 Z" fill="var(--green)"/>
    <path d="M722 10 C810 330 980 470 1140 484 V490 C975 478 800 350 716 10 Z" fill="var(--green-light)"/>
  </svg>

  <div class="index-panel">
    <h2 class="panel-title">Índice</h2>
    <ol class="index-list">
      <li><span class="num">1</span><span class="sep">|</span>¿Quiénes somos?</li>
      <li><span class="num">2</span><span class="sep">|</span>Oferta de Valor</li>
      <li><span class="num">3</span><span class="sep">|</span>Nuestros Servicios</li>
      <li><span class="num">4</span><span class="sep">|</span>Productos</li>
      <li><span class="num">5</span><span class="sep">|</span>Ciclo de administración de Fianzas</li>
      <li><span class="num">6</span><span class="sep">|</span>Nuestros socios de negocio</li>
      <li><span class="num">7</span><span class="sep">|</span>Contacto</li>
    </ol>
  </div>
  <div class="brand brand-index"><span class="mark"></span>TALVORO</div>

  <div class="about-panel">
    <h2 class="panel-title">¿Quiénes<br>somos?</h2>
    <div class="about-text">
      <p>Talvoro bonds, somos un grupo de jóvenes emprendedores, con amplia experiencia en el sector afianzador.</p>
      <p>Estamos convencidos de que nuestro principal diferenciador es la pasión por el servicio.</p>
      <p>Nuestra prioridad es el éxito de cada uno de nuestros clientes, nos aseguramos de que el “trámite” de fianzas deje de ser un “trámite” y se convierta en la llave del éxito para cada uno de nuestros fiados y beneficiarios.</p>
      <p>Buscamos siempre tener relaciones estrechas y de largo plazo con todos nuestros “stakeholders”. Por lo que nos rodeamos del mejor talento en el sector para garantizar a nuestros clientes un servicio personalizado, en tiempo y confiable.</p>
    </div>
  </div>
  <div class="brand brand-about"><span class="mark"></span>TALVORO</div>
</section>
</body>
</html>
```